Emerging Ed-Tech Startup seeking Stationery Designs!

We are in need of basic set of stationery designs to be used for our business operations, letters, emails, and in-office materials. We are a technology startup enhancing on campus work experience offerings by establishing a collaborative work environment for the completion of such tasks.

Our colors are Vibrant Tiffany Blue/Black/White.

Website: www.campusnorthway.com (Still under construction aside from the landing pages)

Please make sure the designs use a brighter more vibrant tiffany blue color than seen in the image files uploaded. We are not using those materials.

Our logo has been added as a file as well, please use that for any designs (include that logo). Thank you.

```html
<!DOCTYPE html>
<html lang="en">
<head>
<meta charset="utf-8">
<title>Campus Northway Stationery Set</title>
<link href="https://fonts.googleapis.com/css2?family=Arimo:wght@400;700&display=swap" rel="stylesheet">
<style>
:root{
  --tiffany:#0ae8e6;
  --ink:#0a0a0a;
  --paper:#ffffff;
  --stage:#e9e6e1;
  --rule:#333333;
  --ghost:#e4e8ea;
  --muted:#444444;
}
*{margin:0;padding:0;box-sizing:border-box}
html,body{width:1200px;height:683px;overflow:hidden}
body{background:var(--stage);font-family:'Arimo',Arial,sans-serif;color:var(--ink);position:relative}
.sheet{position:absolute;background:var(--paper);border:1px solid #9a9a9a;overflow:hidden}
.brand{position:absolute;display:flex;align-items:center;gap:5px;font-weight:700;color:var(--ink);line-height:1;text-transform:uppercase}
.brand .mark{width:12px;height:12px;background:var(--tiffany);flex:none}
.brand .name{font-size:13px;letter-spacing:.3px}
.contact{position:absolute;font-size:7px;color:var(--ink);line-height:12px}
.contact.boxed{border-left:1px solid #999;padding-left:4px}
.footer{position:absolute;left:0;width:100%}
.footer svg{position:absolute;left:0;top:0;display:block}
.footer .txt{position:absolute;font-size:6.5px;white-space:nowrap;letter-spacing:.3px}
.on-dark{color:var(--paper)}
.watermark{position:absolute;font-weight:700;color:var(--ghost);text-transform:uppercase;line-height:1;text-align:center}

/* letterhead */
.letterhead{left:27px;top:18px;width:351px;height:455px}
/* fax */
.fax{left:417px;top:18px;width:351px;height:455px}
.fax-title{position:absolute;left:25px;top:98px;font-size:20px;font-weight:400}
.fax-field{position:absolute;height:12px;border-bottom:1px solid var(--rule);font-size:8.5px;padding-bottom:2px}
.fax-field span{position:absolute;bottom:3px}
/* envelopes */
.envelope{left:790px;width:393px}
.envelope .flap{position:absolute;left:0;top:0;width:100%;display:flex;align-items:center;justify-content:center;border-bottom:1px solid #666}
.flap.light{background:var(--paper)}
.flap.dark{background:var(--ink)}
.flap.tiffany{background:var(--tiffany)}
.flap .brand{position:static}
/* email signature */
.signature{left:22px;top:526px;width:373px;height:102px}
.person{position:absolute;right:12px;top:12px;text-align:right;text-transform:uppercase}
.person .who{font-size:9.5px;letter-spacing:.5px}
.person .role{font-size:7px;margin-top:4px;letter-spacing:.3px}
.caption{position:absolute;left:135px;top:641px;font-size:19px;color:#555}
/* business envelope */
.business{left:456px;top:497px;width:393px;height:170px}
</style>
</head>
<body>

<!-- Letterhead -->
<section class="sheet letterhead" aria-label="Letterhead">
  <div class="brand" style="left:18px;top:20px"><span class="mark"></span><span class="name">Campus<br>Northway</span></div>
  <div class="contact boxed" style="left:259px;top:30px">Unit#B-14 Harbor Lane</div>
  <div class="watermark" style="left:60px;top:200px;width:230px;font-size:40px">Campus<br>Northway</div>
  <div class="footer" style="top:433px;height:21px">
    <svg width="351" height="21" viewBox="0 0 351 21" aria-hidden="true">
      <rect width="351" height="21" fill="var(--ink)"/>
      <path d="M0 0H232C240 0 242 5 252 5H0Z" fill="var(--tiffany)"/>
    </svg>
    <span class="txt on-dark" style="left:10px;top:9px">&#9742; +91 20 4417208 &nbsp;&#9743; +91 14 5528391 &nbsp;&#9679; www.campusnorthway.com</span>
    <span class="txt on-dark" style="left:243px;top:9px">&#8962; Unit#B-14 Harbor Lane</span>
  </div>
</section>

<!-- Fax sheet -->
<section class="sheet fax" aria-label="Fax cover sheet">
  <div class="brand" style="left:25px;top:20px"><span class="mark"></span><span class="name">Campus<br>Northway</span></div>
  <div class="contact boxed" style="left:248px;top:20px">&#9742; +91 20 4417208<br>&#9743; +91 14 5528391<br>&#9679; www.campusnorthway.com</div>
  <h1 class="fax-title">FAX</h1>
  <div class="fax-field" style="left:28px;top:148px;width:293px"><span style="left:1px">To</span><span style="left:191px">From</span></div>
  <div class="fax-field" style="left:28px;top:189px;width:293px"><span style="left:1px">Fax</span><span style="left:191px">Pages</span></div>
  <div class="fax-field" style="left:28px;top:230px;width:293px"><span style="left:1px">Phone</span><span style="left:191px">Date</span></div>
  <div class="fax-field" style="left:28px;top:271px;width:293px"><span style="left:1px">Re</span><span style="left:191px">CC</span></div>
  <div class="footer" style="top:435px;height:20px">
    <svg width="351" height="20" viewBox="0 0 351 20" aria-hidden="true">
      <rect width="351" height="20" fill="var(--tiffany)"/>
      <path d="M215 0H351V20H0V12H200C210 12 208 0 215 0Z" fill="var(--ink)"/>
    </svg>
    <span class="txt on-dark" style="left:243px;top:4px">&#8962; Unit#B-14 Harbor Lane</span>
  </div>
</section>

<!-- Envelope flap variations -->
<section class="sheet envelope" style="top:0;height:186px" aria-label="Envelope, white flap">
  <div class="flap light" style="height:76px"><div class="brand"><span class="mark"></span><span class="name">Campus Northway</span></div></div>
</section>
<section class="sheet envelope" style="top:208px;height:169px" aria-label="Envelope, black flap">
  <div class="flap dark" style="height:59px"><div class="brand" style="color:var(--paper)"><span class="mark" style="background:var(--paper)"></span><span class="name">Campus Northway</span></div></div>
</section>
<section class="sheet envelope" style="top:393px;height:168px" aria-label="Envelope, tiffany flap">
  <div class="flap tiffany" style="height:59px"><div class="brand" style="color:var(--paper)"><span class="mark" style="background:var(--paper)"></span><span class="name">Campus Northway</span></div></div>
</section>

<!-- Email signature -->
<section class="sheet signature" aria-label="Email signature">
  <div class="brand" style="left:12px;top:14px"><span class="mark"></span><span class="name" style="font-size:11px">Campus<br>Northway</span></div>
  <div class="person"><div class="who">Mr. Owen Hartley</div><div class="role">Marketing Manager</div></div>
  <div class="footer" style="top:78px;height:24px">
    <svg width="373" height="24" viewBox="0 0 373 24" aria-hidden="true">
      <rect width="373" height="24" fill="var(--ink)"/>
      <path d="M0 0H245C255 0 255 10 265 10H0Z" fill="var(--tiffany)"/>
    </svg>
    <span class="txt" style="left:20px;top:2px">&#9742; +91 20 4417208 &nbsp;&#9743; +91 14 5528391 &nbsp;&#9679; www.campusnorthway.com</span>
    <span class="txt on-dark" style="left:262px;top:2px">&#8962; Unit#B-14 Harbor Lane</span>
  </div>
</section>
<p class="caption">Email Signature</p>

<!-- Business envelope -->
<section class="sheet business" aria-label="Business envelope">
  <div class="brand" style="left:15px;top:16px"><span class="mark"></span><span class="name">Campus<br>Northway</span></div>
  <div class="contact" style="left:15px;top:64px;font-size:6.5px">Unit#B-14 Harbor Lane</div>
  <div class="watermark" style="right:14px;top:100px;font-size:11px">Campus<br>Northway</div>
  <div class="footer" style="top:147px;height:23px">
    <svg width="393" height="23" viewBox="0 0 393 23" aria-hidden="true">
      <rect width="393" height="23" fill="var(--ink)"/>
      <path d="M0 0H393V0H270C258 0 258 12 245 12H0Z" fill="var(--tiffany)"/>
      <rect width="393" height="0" fill="var(--tiffany)"/>
    </svg>
    <span class="txt" style="left:15px;top:3px;font-size:6px">www.campusnorthway.com</span>
  </div>
</section>

</body>
</html>
```